Retail swing tag labels for a sale / reduction

We need some graphics done to be made into retail swing tag labels, for the purpose of reductions on selected products.

We have attached 2 examples of previous designs that were similar idea, but more themed for 'autumn' and 'winter'. This theme will just have the word 'REDUCED'.

The white areas can be smaller in size, as we would like to include a large "20% OFF" at the bottom, and then a 30%, 40%, 50% option.

Overall colour scheme should be red background with some form of detailed patterning (see previous examples). Bright and e-catching.

Any other questions, just ask.

The screenshot is front the printers, but in horizontal orientation.

The finished dimensions will be A6 portrait, printed both sides.

We have also included the vector file of the shop "Hollowmere Furnishings", which can be included on 1 of the sides.

```html
<!DOCTYPE html>
<html lang="en">
<head>
<meta charset="utf-8">
<title>Reduced Swing Tags</title>
<link rel="stylesheet" href="https://fonts.googleapis.com/css2?family=Anton&family=Montserrat:ital,wght@0,400;0,800;0,900;1,800&display=swap">
<style>
  :root {
    --backdrop: #fcd900;
    --red-bright: #e3161c;
    --red-mid: #b50f16;
    --red-deep: #6e060b;
    --red-shade: #2e0204;
    --head-top: #ffe14a;
    --head-bottom: #f7861a;
    --head-edge: #ffc21a;
    --tag-red: #d0161d;
    --tag-dark: #8f0c11;
    --price-red: #e3101c;
    --white: #ffffff;
  }
  html, body {
    margin: 0;
    padding: 0;
    width: 1200px;
    height: 927px;
    overflow: hidden;
    background: var(--backdrop);
  }
  .sheet {
    position: relative;
    width: 1200px;
    height: 927px;
    border: 1px solid #222;
    box-sizing: border-box;
  }
  .tag-card {
    position: absolute;
    top: 40px;
    width: 464px;
    height: 648px;
    box-shadow: 4px 5px 6px rgba(0,0,0,0.35);
    overflow: hidden;
  }
  .tag-card--front { left: 121px; }
  .tag-card--back { left: 615px; }
  .tag-card svg { display: block; }
  .red-backdrop {
    position: absolute;
    inset: 0;
    background:
      radial-gradient(ellipse 48% 30% at 50% 40%, rgba(46,2,4,0.9), rgba(60,4,6,0.5) 55%, rgba(0,0,0,0) 100%),
      radial-gradient(circle at 18% 12%, var(--red-bright), transparent 38%),
      radial-gradient(circle at 85% 88%, var(--red-bright), transparent 40%),
      radial-gradient(circle at 88% 22%, var(--red-deep), transparent 35%),
      radial-gradient(circle at 12% 78%, var(--red-deep), transparent 35%),
      linear-gradient(160deg, var(--red-mid), var(--red-bright) 50%, var(--red-mid));
  }
  .tag-art {
    position: absolute;
    inset: 0;
  }
  .headline {
    font-family: "Montserrat", sans-serif;
    font-weight: 900;
  }
  .price-label {
    font-family: "Montserrat", sans-serif;
    font-weight: 800;
    font-style: italic;
    fill: var(--price-red);
  }
  .discount {
    font-family: "Anton", sans-serif;
    fill: var(--white);
  }
  .brand {
    position: absolute;
    left: 0;
    right: 0;
    top: 570px;
    text-align: center;
    font-family: "Montserrat", sans-serif;
    font-weight: 400;
    font-size: 13px;
    letter-spacing: 2px;
    color: var(--white);
    text-transform: uppercase;
  }
  .brand-mark {
    display: block;
    width: 50px;
    height: 40px;
    margin: 0 auto 10px;
    border: 1px solid var(--white);
  }
  .option-row {
    position: absolute;
    left: 121px;
    top: 720px;
    width: 958px;
    display: flex;
    justify-content: space-between;
  }
  .option-tag { display: block; }
</style>
</head>
<body>
<div class="sheet">

  <svg width="0" height="0" style="position:absolute">
    <defs>
      <linearGradient id="headFill" x1="0" y1="0" x2="0" y2="1">
        <stop offset="0" stop-color="var(--head-top)"/>
        <stop offset="1" stop-color="var(--head-bottom)"/>
      </linearGradient>
      <linearGradient id="tagFill" x1="0" y1="0" x2="0" y2="1">
        <stop offset="0" stop-color="var(--tag-red)"/>
        <stop offset="1" stop-color="var(--tag-dark)"/>
      </linearGradient>
    </defs>
  </svg>

  <section class="tag-card tag-card--front">
    <div class="red-backdrop" role="img" aria-label="Bright red backdrop with detailed patterning and a dark centre"></div>
    <svg class="tag-art" width="464" height="648" viewBox="0 0 464 648">
      <g class="headline">
        <text x="41" y="302" font-size="92" textLength="390" lengthAdjust="spacingAndGlyphs" fill="var(--red-shade)">REDUCED</text>
        <text x="38" y="299" font-size="92" textLength="390" lengthAdjust="spacingAndGlyphs" fill="var(--head-edge)">REDUCED</text>
        <text x="35" y="295" font-size="92" textLength="390" lengthAdjust="spacingAndGlyphs" fill="url(#headFill)" stroke="var(--white)" stroke-width="3" paint-order="stroke">REDUCED</text>
      </g>
    </svg>
    <div class="brand"><span class="brand-mark"></span>Hollowmere Furnishings</div>
  </section>

  <section class="tag-card tag-card--back">
    <div class="red-backdrop" role="img" aria-label="Bright red backdrop with detailed patterning and a dark centre"></div>
    <svg class="tag-art" width="464" height="648" viewBox="0 0 464 648">
      <g class="headline" transform="rotate(-4 232 170)">
        <text x="41" y="207" font-size="92" textLength="390" lengthAdjust="spacingAndGlyphs" fill="var(--red-shade)">REDUCED</text>
        <text x="38" y="204" font-size="92" textLength="390" lengthAdjust="spacingAndGlyphs" fill="var(--head-edge)">REDUCED</text>
        <text x="35" y="200" font-size="92" textLength="390" lengthAdjust="spacingAndGlyphs" fill="url(#headFill)" stroke="var(--white)" stroke-width="3" paint-order="stroke">REDUCED</text>
      </g>

      <rect class="price-box" x="73" y="262" width="318" height="170" fill="var(--white)"/>
      <text class="price-label" x="98" y="312" font-size="26">WAS £</text>
      <text class="price-label" x="98" y="396" font-size="26">NOW</text>
      <text class="price-label" x="184" y="402" font-size="46">£</text>

      <g class="discount-tag">
        <polygon points="52,484 329,458 420,509 354,593 67,617" fill="rgba(0,0,0,0.35)" transform="translate(3 5)"/>
        <polygon points="50,480 327,454 418,505 352,589 65,613" fill="url(#tagFill)" stroke="var(--white)" stroke-width="2"/>
        <circle cx="352" cy="520" r="14" fill="#d9d9d9" stroke="#8a8a8a" stroke-width="3"/>
        <circle cx="352" cy="520" r="8" fill="var(--tag-red)"/>
        <g transform="rotate(-5 180 540)">
          <text class="discount" x="78" y="588" font-size="112">20</text>
          <text class="discount" x="190" y="534" font-size="46">%</text>
          <text class="discount" x="190" y="582" font-size="50">OFF</text>
        </g>
      </g>
    </svg>
  </section>

  <div class="option-row">
    <svg class="option-tag" width="300" height="150" viewBox="0 0 300 150">
      <polygon points="8,30 210,12 292,62 226,128 16,142" fill="rgba(0,0,0,0.3)" transform="translate(3 4)"/>
      <polygon points="6,28 208,10 290,60 224,126 14,140" fill="url(#tagFill)" stroke="var(--white)" stroke-width="2"/>
      <circle cx="232" cy="70" r="11" fill="#d9d9d9" stroke="#8a8a8a" stroke-width="3"/>
      <circle cx="232" cy="70" r="6" fill="var(--tag-red)"/>
      <g transform="rotate(-5 110 80)">
        <text class="discount" x="26" y="118" font-size="86">30</text>
        <text class="discount" x="112" y="76" font-size="36">%</text>
        <text class="discount" x="112" y="114" font-size="38">OFF</text>
      </g>
    </svg>
    <svg class="option-tag" width="300" height="150" viewBox="0 0 300 150">
      <polygon points="8,30 210,12 292,62 226,128 16,142" fill="rgba(0,0,0,0.3)" transform="translate(3 4)"/>
      <polygon points="6,28 208,10 290,60 224,126 14,140" fill="url(#tagFill)" stroke="var(--white)" stroke-width="2"/>
      <circle cx="232" cy="70" r="11" fill="#d9d9d9" stroke="#8a8a8a" stroke-width="3"/>
      <circle cx="232" cy="70" r="6" fill="var(--tag-red)"/>
      <g transform="rotate(-5 110 80)">
        <text class="discount" x="26" y="118" font-size="86">40</text>
        <text class="discount" x="112" y="76" font-size="36">%</text>
        <text class="discount" x="112" y="114" font-size="38">OFF</text>
      </g>
    </svg>
    <svg class="option-tag" width="300" height="150" viewBox="0 0 300 150">
      <polygon points="8,30 210,12 292,62 226,128 16,142" fill="rgba(0,0,0,0.3)" transform="translate(3 4)"/>
      <polygon points="6,28 208,10 290,60 224,126 14,140" fill="url(#tagFill)" stroke="var(--white)" stroke-width="2"/>
      <circle cx="232" cy="70" r="11" fill="#d9d9d9" stroke="#8a8a8a" stroke-width="3"/>
      <circle cx="232" cy="70" r="6" fill="var(--tag-red)"/>
      <g transform="rotate(-5 110 80)">
        <text class="discount" x="26" y="118" font-size="86">50</text>
        <text class="discount" x="112" y="76" font-size="36">%</text>
        <text class="discount" x="112" y="114" font-size="38">OFF</text>
      </g>
    </svg>
  </div>

</div>
</body>
</html>
```